TEBSIRK HOA Portal Site for Public

Clean up and organize current website; need website to look good and functional; this is a HOA (homeowner association management) website where homeowners can login and pay their bill, general information about a HOA, monthly newsletter page.
Competitors:
https://quillmarsh.example/
https://dorvinpalms.example/
https://www.kelbrookhomes.example/nevada
http://www.tpw-hoa.example/

Target Market(s)

homeowners

Industry/Entity Type

Real Estate

Coding

Coded - Design and coding required

Number of Pages Required

5+ page

Font styles to use
Serif

Colors
0292cd
33a6d7
e667a6
e34297

Requirements
Must have
• login to pay
• services page
• contact us
• order resale package
Nice to have
• page why an HOA would contract us

```html
<!DOCTYPE html>
<html lang="en">
<head>
<meta charset="utf-8">
<title>Tebsirk Association Management</title>
<link href="https://fonts.googleapis.com/css2?family=Lato:wght@400;700;900&family=Roboto:ital,wght@0,400;0,500;1,400&display=swap" rel="stylesheet">
<style>
:root{
  --blue:#2a93cf;
  --blue-light:#33a6d7;
  --pink:#e34297;
  --pink-soft:#e0479a;
  --ink:#333;
  --grey-bg:#f0f0f0;
  --footer:#2c2c2e;
  --footer-deep:#1f1f21;
  --footer-text:#b9b9bd;
}
*{box-sizing:border-box;margin:0;padding:0}
html,body{width:1200px;height:3382px;overflow:hidden}
body{position:relative;font-family:"Roboto",sans-serif;color:var(--ink);background:#fff}
.abs{position:absolute}
.btn{position:absolute;display:flex;align-items:center;justify-content:center;border-radius:22px;color:#fff;font:700 14px "Roboto",sans-serif;letter-spacing:.4px;text-transform:uppercase}
.btn-pink{background:var(--pink)}
.btn-blue{background:var(--blue)}
.center{left:0;width:1200px;text-align:center}
h2{font-family:"Lato",sans-serif;font-weight:700;font-size:35px;text-transform:uppercase;letter-spacing:.3px}

/* header */
.topline{top:0;left:0;width:1200px;height:4px;background:var(--blue)}
.brand{top:38px;left:75px;display:flex;align-items:center;gap:12px}
.brand-square{width:46px;height:46px;background:#5da83a}
.brand-name{font:900 15px "Lato",sans-serif;color:#222;letter-spacing:.2px;width:170px;line-height:1.25}
.nav{top:91px;right:73px;display:flex;gap:24px;font:500 14px "Roboto",sans-serif;text-transform:uppercase;color:#222}
.nav .active{color:var(--blue);border-bottom:3px solid var(--blue);padding-bottom:6px}

/* hero */
.hero{top:133px;left:0;width:1200px;height:577px;background:linear-gradient(120deg,#5d4a3c 0%,#a08a74 35%,#6f7c8c 65%,#2f4a78 100%)}
.hero-title{top:330px;font:900 55px "Lato",sans-serif;color:#fff;text-shadow:0 2px 6px rgba(0,0,0,.35)}
.hero-sub{top:400px;font:400 26px "Lato",sans-serif;color:#fff;text-shadow:0 1px 4px rgba(0,0,0,.4)}
.dot{position:absolute;width:9px;height:9px;border-radius:50%;background:#fff}

/* about */
.about{top:710px;left:0;width:1200px;height:397px;background:var(--grey-bg)}
.about h2{color:var(--blue);top:766px}
.about-text{top:822px;left:70px;width:1060px;text-align:center;font-size:16px;line-height:29px;color:#333}

/* services */
.svc-photo{top:1169px;left:75px;width:512px;height:372px;background:linear-gradient(135deg,#1e2430,#6a7788 55%,#cfd5dd)}
.svc h2{top:1160px;left:616px;color:var(--blue);position:absolute}
.svc-list{top:1222px;left:616px;width:480px;list-style:none;font-size:16px;line-height:26px;color:#333}
.svc-list li{display:flex;gap:18px;margin-bottom:11px}
.svc-list svg{flex:none;margin-top:6px}

/* testimonials */
.testi{top:1612px;left:0;width:1200px;height:581px;background:linear-gradient(30deg,#dc4c98 0%,#8a6fb6 50%,#2c94d0 100%)}
.testi h2{color:#fff;top:1678px}
.testi-sub{top:1742px;font:300 18px/29px "Roboto",sans-serif;color:#f3eaf7}
.card{position:absolute;top:1836px;width:513px;height:225px;background:#fff}
.quote{padding:24px 40px 0;text-align:center;font:italic 16px/29px "Roboto",sans-serif;color:#333;height:122px}
.card hr{border:0;border-top:1px solid #cfcfcf;margin:0 29px}
.person{display:flex;align-items:center;justify-content:center;gap:20px;margin-top:14px}
.avatar{width:68px;height:68px;border-radius:50%;background:linear-gradient(135deg,#8b6650,#d9b59a)}
.pname{font:700 16px "Roboto",sans-serif;color:var(--blue)}
.ploc{font-size:13px;color:#444;margin-top:4px}

/* blog */
.blog h2{color:var(--blue);top:2241px}
.post{position:absolute;top:2308px;width:330px}
.post-img{height:206px}
.post h3{margin-top:20px;font:700 22px/29px "Lato",sans-serif;color:var(--blue)}
.post p{margin-top:12px;font-size:15px;line-height:25px;color:#444}
.read{margin-top:14px;font:500 15px "Roboto",sans-serif;color:var(--pink);display:flex;align-items:center;gap:8px}

/* newsletter */
.news{top:2731px;left:0;width:1200px;height:250px;background:var(--pink-soft)}
.news h2{color:#fff;top:2782px}
.news-sub{top:2833px;font-size:16px;color:#fff}
.email{top:2878px;left:340px;width:360px;height:42px;border-radius:21px;background:#fff;font-size:14px;color:#444;padding:14px 26px}
.signup{top:2878px;left:708px;width:144px;height:42px;font-size:17px;font-weight:500}

/* footer */
.footer{top:2981px;left:0;width:1200px;height:299px;background:var(--footer)}
.fcol{position:absolute;top:3029px;font-size:13px;line-height:25px;color:var(--footer-text)}
.fcol h4{font:500 18px "Lato",sans-serif;color:var(--blue-light);margin-bottom:12px}
.fcol ul{list-style:none}
.fcol li{line-height:34px}
.fcol strong{color:#fff;font-weight:700;font-size:14px}
.crow{display:flex;gap:18px;align-items:center}
.bottom{top:3280px;left:0;width:1200px;height:102px;background:var(--footer-deep)}
.copy{top:3325px;left:146px;font-size:12px;color:var(--footer-text)}
.fbrand{top:3318px;left:75px;display:flex;align-items:center;gap:10px;font:700 14px "Lato",sans-serif;color:#9a9aa0}
.fbrand span.sq{width:26px;height:26px;background:#6a6a70}
.social{top:3316px;left:960px;display:flex;gap:6px}
.social span{width:28px;height:28px;border-radius:50%;background:#8e8e93}
.social span.on{background:#fff}
</style>
</head>
<body>

<div class="abs topline"></div>
<div class="abs brand"><span class="brand-square"></span><span class="brand-name">TEBSIRK ASSOCIATION MANAGEMENT</span></div>
<div class="btn btn-blue" style="top:25px;left:779px;width:140px;height:37px;font-size:13px">Log In Pay</div>
<div class="btn btn-pink" style="top:25px;left:934px;width:193px;height:37px;font-size:13px">Homeowners Log In</div>
<nav class="abs nav">
  <span class="active">Home</span><span>About</span><span>Partner With Us</span><span>Elements of Living</span><span>Contact Us</span>
</nav>

<section>
  <div class="abs hero" role="img" aria-label="Photo of three professionals smiling around a table while reviewing documents"></div>
  <div class="abs center hero-title">Association Management Services</div>
  <div class="abs center hero-sub">TEBSIRK manages communities throughout Southern Nevada.</div>
  <div class="btn btn-pink" style="top:462px;left:515px;width:170px;height:38px">Learn More</div>
  <svg class="abs" style="top:418px;left:62px" width="24" height="44" viewBox="0 0 24 44"><path d="M20 4 4 22l16 18" fill="none" stroke="#fff" stroke-opacity=".8" stroke-width="5"/></svg>
  <svg class="abs" style="top:418px;left:1116px" width="24" height="44" viewBox="0 0 24 44"><path d="M4 4l16 18L4 40" fill="none" stroke="#fff" stroke-opacity=".8" stroke-width="5"/></svg>
  <span class="dot" style="top:650px;left:579px;opacity:.5"></span>
  <span class="dot" style="top:650px;left:596px"></span>
  <span class="dot" style="top:650px;left:613px"></span>
</section>

<section class="about-sec">
  <div class="abs about"></div>
  <div class="about"><h2 class="abs center" style="top:766px;color:var(--blue)">About Tebsirk Association Management</h2></div>
  <p class="abs about-text">Nam vulputate justo vitae aliquam semper. Suspendisse auctor dui a augue tempor cursus. Nullam vitae ipsum eu turpis blandit semper eu et felis. Nulla facilisi. Suspendisse eget varius ligula, sit amet accumsan sapien. Phasellus et euismod nisi, et tristique odio. Donec quis tortor suscipit, feugiat massa eget, facilisis ipsum. Donec eu mollis nisi, vel molestie leo. Fusce tincidunt tortor dictum semper commodo.<br>Morbi non eros lacinia, rhoncus metus at, ultricies tellus. Ut efficitur felis in nisi molestie pretium. Pellentesque habitant morbi tristique senectus et netus et malesuada fames ac turpis egestas.</p>
  <div class="btn btn-pink" style="top:994px;left:515px;width:170px;height:39px">Learn More</div>
</section>

<section class="svc">
  <div class="abs svc-photo" role="img" aria-label="Photo of business people reviewing financial charts on a tablet and papers"></div>
  <h2>Service We Offers</h2>
  <ul class="abs svc-list">
    <li><svg width="14" height="14" viewBox="0 0 14 14"><circle cx="7" cy="7" r="7" fill="var(--blue)"/><path d="M3.8 7.2l2.2 2.2 4.2-4.4" fill="none" stroke="#fff" stroke-width="1.8"/></svg>Accessible, licensed Association Managers</li>
    <li><svg width="14" height="14" viewBox="0 0 14 14"><circle cx="7" cy="7" r="7" fill="var(--blue)"/><path d="M3.8 7.2l2.2 2.2 4.2-4.4" fill="none" stroke="#fff" stroke-width="1.8"/></svg>24 hour Web site access: online account information</li>
    <li><svg width="14" height="14" viewBox="0 0 14 14"><circle cx="7" cy="7" r="7" fill="var(--blue)"/><path d="M3.8 7.2l2.2 2.2 4.2-4.4" fill="none" stroke="#fff" stroke-width="1.8"/></svg>24 hour emergency service</li>
    <li><svg width="14" height="14" viewBox="0 0 14 14"><circle cx="7" cy="7" r="7" fill="var(--blue)"/><path d="M3.8 7.2l2.2 2.2 4.2-4.4" fill="none" stroke="#fff" stroke-width="1.8"/></svg>Provide monthly financial reports to the Board of Directors</li>
    <li><svg width="14" height="14" viewBox="0 0 14 14"><circle cx="7" cy="7" r="7" fill="var(--blue)"/><path d="M3.8 7.2l2.2 2.2 4.2-4.4" fill="none" stroke="#fff" stroke-width="1.8"/></svg>Read, study and understand all governing documents of the Association.</li>
    <li><svg width="14" height="14" viewBox="0 0 14 14"><circle cx="7" cy="7" r="7" fill="var(--blue)"/><path d="M3.8 7.2l2.2 2.2 4.2-4.4" fill="none" stroke="#fff" stroke-width="1.8"/></svg>Prepare the annual budget for Board approval</li>
  </ul>
  <div class="btn btn-pink" style="top:1503px;left:616px;width:170px;height:39px">Learn More</div>
</section>

<section>
  <div class="abs testi"></div>
  <h2 class="abs center" style="top:1678px;color:#fff">Customer Testimonials</h2>
  <p class="abs center testi-sub">Aliquam molestie, mi et imperdiet euismod, dui purus auctor tellus, et interdum lacus lectus et ante<br>Sed accumsan sollicitudin sapien, sit amet adipiscing turpis gravida ac.</p>
  <div class="card" style="left:75px">
    <p class="quote">“ Samen met Veldmaar een aantal projecten gedaan. Het zijn gedreven personen met een passie voor softwareontwikkeling....”</p>
    <hr>
    <div class="person"><div class="avatar" role="img" aria-label="Customer portrait"></div><div><div class="pname">Name Heading</div><div class="ploc">Location</div></div></div>
  </div>
  <div class="card" style="left:614px">
    <p class="quote">“ Veldmaar heeft ons veder geholpen toen het project vastliep. Hun duidelijke stappenplan zorgde dat de deadlines gehaald werden en het product snel online stond....”</p>
    <hr>
    <div class="person"><div class="avatar" role="img" aria-label="Customer portrait"></div><div><div class="pname">Name Heading</div><div class="ploc">Location</div></div></div>
  </div>
  <span class="dot" style="top:2118px;left:573px;width:8px;height:8px"></span>
  <span class="dot" style="top:2118px;left:589px;width:8px;height:8px"></span>
  <span class="dot" style="top:2118px;left:605px;width:8px;height:8px;background:#222"></span>
  <span class="dot" style="top:2118px;left:621px;width:8px;height:8px"></span>
</section>

<section class="blog">
  <h2 class="abs center" style="top:2241px;color:var(--blue)">Blog</h2>
  <article class="post" style="left:75px">
    <div class="post-img" role="img" aria-label="Photo of a waterfront city skyline under a blue sky" style="background:linear-gradient(180deg,#8fc2e6 0%,#c9d8e2 45%,#4b7fa8 75%,#2d5f8e 100%)"></div>
    <h3>Aging Gracefully The Retirement Industry in South Florida</h3>
    <p>Vestibulum ante ipsum primis in faucibus orci luctus et ultrices posuere.</p>
    <div class="read">Read More <svg width="16" height="8" viewBox="0 0 16 8"><path d="M0 4h13M10 1l3 3-3 3" fill="none" stroke="var(--pink)" stroke-width="1.8"/></svg></div>
  </article>
  <article class="post" style="left:436px">
    <div class="post-img" role="img" aria-label="Photo of a doorman greeting an elderly resident with a walker in a lobby" style="background:linear-gradient(90deg,#2a1f1a 0%,#6b4c35 45%,#c9b59a 60%,#3a2a20 100%)"></div>
    <h3>Elderly New Yorkers, Here for the Duration</h3>
    <p>Vestibulum ante ipsum primis in faucibus orci luctus et ultrices posuere</p>
    <div class="read">Read More <svg width="16" height="8" viewBox="0 0 16 8"><path d="M0 4h13M10 1l3 3-3 3" fill="none" stroke="var(--pink)" stroke-width="1.8"/></svg></div>
  </article>
  <article class="post" style="left:796px">
    <div class="post-img" role="img" aria-label="Photo of a hand signing a document beside a small wooden house model" style="background:linear-gradient(135deg,#f4f1ec 0%,#e8ddd0 50%,#c49a6c 80%,#e9e4de 100%)"></div>
    <h3>How to Apply the Right Criteria to Evaluate Property</h3>
    <p>Vestibulum ante ipsum primis in faucibus orci luctus et ultrices posuere.</p>
    <div class="read">Read More <svg width="16" height="8" viewBox="0 0 16 8"><path d="M0 4h13M10 1l3 3-3 3" fill="none" stroke="var(--pink)" stroke-width="1.8"/></svg></div>
  </article>
</section>

<section>
  <div class="abs news"></div>
  <h2 class="abs center" style="top:2782px;color:#fff">Monthly Newsletter</h2>
  <p class="abs center news-sub">Vestibulum ante ipsum primis in faucibus orci luctus et ultrices posuere vitae aliquam semper.</p>
  <div class="abs email">Enter Email Address</div>
  <div class="btn btn-blue signup">SIGN UP</div>
</section>

<footer>
  <div class="abs footer"></div>
  <div class="fcol" style="left:76px;width:310px">
    <h4>Tebsirk Association Management</h4>
    As the leading residential property management company in North America, we work hard to help your community thrive. Our dedication, responsiveness and integrity are why thousands of communities across the U.S. and Canada
  </div>
  <div class="fcol" style="left:452px">
    <h4>Site Map</h4>
    <ul style="margin-top:-8px"><li>Home</li><li>About</li><li>Partner With Us</li><li>Elements Of living</li><li>Contact Us</li></ul>
  </div>
  <div class="fcol" style="left:658px">
    <h4>Services</h4>
    <ul style="margin-top:-8px"><li>Morbi non eros</li><li>Lacinia rhoncus metus</li><li>Ultricies tellus</li><li>Aliquam ac massa</li><li>Nulla eleifend</li></ul>
  </div>
  <div class="fcol" style="left:884px;width:260px">
    <h4>Contact Info</h4>
    <strong>Tebsirk Association Management</strong><br>
    2260 Larkspur Way Henderson,<br>NV 89000<br>
    <div class="crow"><svg width="12" height="12" viewBox="0 0 12 12"><path d="M2 1l2.5 0 1 3-1.5 1a7 7 0 0 0 3 3l1-1.5 3 1V11C6 11 1 6 2 1z" fill="#b9b9bd"/></svg><span>(555) 014-2297</span></div>
    <div class="crow"><svg width="12" height="10" viewBox="0 0 12 10"><rect width="12" height="10" fill="#b9b9bd"/><path d="M0 0l6 5 6-5" fill="none" stroke="#2c2c2e" stroke-width="1.2"/></svg><span>office@tebsirk.example</span></div>
  </div>
  <div class="abs bottom"></div>
  <div class="abs fbrand"><span class="sq"></span></div>
  <div class="abs copy">Copyright © 2019 Company Name .All Right Reserved</div>
  <div class="abs social" aria-label="Social links"><span></span><span class="on"></span><span></span><span></span><span></span></div>
</footer>

</body>
</html>
```